"Career in Gradvel" | Poster design

We need a "We are hiring" poster design. We are a construction company based in Croatia and we are looking for 3 categories of construction workers. We want moder, serious and powerful poster . In attachment you can find our logo. The font of a text that is used in logo design is "nexa bold".

At the bottom (or where designer can see it) will be description of general condition. The poster must be simple and clear.

Target Market(s)

Wide range of employment

Industry/Entity Type

Construction Company

Colors

Designer to choose colors to be used in the design.

Requirements
Must have
• The text in poster that will be needed is "Mason/carpenter job", "Steel-bender job" and "Auxiliary worker". This terms may be wrong, but it will be translated in local language. Under all of them will be a short descrtiption row, and one row of salary. This is for all three categories.
• At the bottom (or where designer can see it) will be description of general condition. The poster must be simple and clear.

```html
<!DOCTYPE html>
<html lang="en">
<head>
<meta charset="utf-8">
<title>Gradvel – Finding the Right Candidate</title>
<link rel="stylesheet" href="https://fonts.googleapis.com/css2?family=Bebas+Neue&family=Montserrat:wght@500&family=Arimo:wght@400;700&display=swap">
<style>
  :root {
    --surround: #6f6f6f;
    --paper: #f4f5f6;
    --paper-edge: #e3e5e8;
    --stripe: rgba(0, 0, 0, 0.035);
    --ink: #2b2b2b;
    --orange: #ee7f22;
    --frame: #c8c8c8;
    --rule: #c9c9c9;
    --crowd-warm: #e9b58c;
    --crowd-mid: #c9c2bb;
    --crowd-cool: #aab6c4;
    --scene-light: #fbfbfb;
  }
  * { box-sizing: border-box; margin: 0; padding: 0; }
  html, body {
    width: 846px; height: 1200px; overflow: hidden;
    background: var(--surround);
  }
  .poster {
    position: absolute; left: 32px; top: 48px;
    width: 781px; height: 1105px;
    background:
      repeating-linear-gradient(-30deg, var(--stripe) 0 1px, transparent 1px 6px),
      radial-gradient(ellipse at 50% 40%, #ffffff 0%, var(--paper) 60%, var(--paper-edge) 100%);
    font-family: "Arimo", Arial, sans-serif;
    color: var(--ink);
  }
  .brand {
    position: absolute; left: 0; top: 42px; width: 100%;
    text-align: center;
  }
  .brand-square {
    display: block; margin: 0 auto;
    width: 78px; height: 76px;
    border: 3px solid #5a5a5a;
  }
  .brand-name {
    display: block; margin-top: 6px;
    font-family: "Montserrat", sans-serif; font-weight: 500;
    font-size: 31px; letter-spacing: 3px; line-height: 1;
    color: var(--orange); text-transform: uppercase;
  }
  .brand-tagline {
    display: block; margin-top: 2px;
    font-size: 8.5px; font-weight: 700; letter-spacing: 0.2px;
    color: #444;
  }
  .headline {
    position: absolute; left: 0; top: 190px; width: 100%;
    text-align: center;
    font-family: "Bebas Neue", sans-serif; font-weight: 400;
    font-size: 76px; line-height: 72px; letter-spacing: 2px;
    color: var(--ink);
  }
  .headline .accent { color: var(--orange); }
  .crowd-frame {
    position: absolute; left: 157px; top: 362px;
    width: 467px; height: 464px;
    border: 7px solid var(--frame);
    background: var(--scene-light);
  }
  .crowd-art {
    width: 100%; height: 100%;
    background: linear-gradient(160deg, var(--crowd-warm) 0%, var(--crowd-mid) 50%, var(--crowd-cool) 100%);
  }
  .jobs {
    position: absolute; left: 34px; top: 867px;
    width: 714px; height: 85px;
    border-top: 1px solid var(--rule);
    border-bottom: 1px solid var(--rule);
    display: grid; grid-template-columns: 1fr 1fr 1fr;
  }
  .job { padding-top: 11px; text-align: center; }
  .job + .job { border-left: 1px solid var(--rule); margin: 10px 0; padding-top: 1px; }
  .job-title {
    font-family: "Bebas Neue", sans-serif; font-weight: 400;
    font-size: 22px; line-height: 22px; letter-spacing: 0.5px;
    color: var(--orange);
  }
  .job-desc, .job-salary {
    font-size: 11px; font-weight: 700; line-height: 13px; color: var(--ink);
  }
  .contact {
    position: absolute; left: 0; top: 990px; width: 100%;
    text-align: center;
    font-size: 19px; font-weight: 700; color: var(--orange);
    letter-spacing: 0.3px;
  }
  .contact .sep { margin: 0 8px; }
  .terms {
    position: absolute; left: 50px; top: 1020px; width: 695px;
    font-size: 7.3px; line-height: 9.6px; color: #333;
  }
</style>
</head>
<body>
  <main class="poster">
    <header class="brand">
      <span class="brand-square"></span>
      <span class="brand-name">Gradvel</span>
      <span class="brand-tagline">IZVOĐENJE I VOĐENJE GRAĐEVINSKIH RADOVA</span>
    </header>

    <h1 class="headline">Finding the<br><span class="accent">Right</span> Candidate</h1>

    <figure class="crowd-frame">
      <div class="crowd-art" role="img" aria-label="Crowd of people standing together to form a large upward arrow with a bar above it"></div>
    </figure>

    <section class="jobs">
      <article class="job">
        <h2 class="job-title">Mason/Carpenter Job</h2>
        <p class="job-desc">of them of them Under all of theof them<br>m will be a short descrtiption row</p>
        <p class="job-salary">Sallery $85000</p>
      </article>
      <article class="job">
        <h2 class="job-title">Steel-Bender Job</h2>
        <p class="job-desc">of them of them Under all of theof them<br>m will be a short descrtiption row</p>
        <p class="job-salary">Sallery $85000</p>
      </article>
      <article class="job">
        <h2 class="job-title">Auxiliary Worker</h2>
        <p class="job-desc">of them of them Under all of theof them<br>m will be a short descrtiption row</p>
        <p class="job-salary">Sallery $85000</p>
      </article>
    </section>

    <p class="contact">ph. 10987654321<span class="sep">|</span>email:&nbsp; jobs@gradvel.com</p>

    <p class="terms">Terms &amp; Condations: is simply dummy text of the printing and typesetting industry. Lorem Ipsum has been the industry's standard dummy text ever since the 1500s, when an unknown printer took a galley of type and scrambled it to make a type specimen book. It has survived not only five centuries, but, remaining essentiTerms &amp; Condations: is simply dummy text of the printing and typesetting industry. Lorem Ipsum has been the industry's standard dummy text ever since the 1500s, when an unknown printer took a galley of type and scrambled it to make a type specimen book. It has survived not only five centuries, but, remaining essentially unchanged.ally unchanged.</p>
  </main>
</body>
</html>
```